Update informational website

I need a new modern site design for my website.

Here is the site: http://q.zq/kpTr

Here is a theme I liked: http://q.zq/kpTm

I am looking for something with clean lines and an exciting designs and graphics, please use images from brindlecove.com and track the images used so I can buy them if I like the design.

I just need the homepage and one interior page designed.

Colors
Bright Green #6ed30d
Dark Text #222
Lighter Text #444

Number of Pages Required

2 page

Font styles to use
Sans Serif

Requirements
Must have
• Clean, good spacing, responsive design, high resolution design

```html
<!DOCTYPE html>
<html lang="en">
<head>
<meta charset="utf-8">
<title>Saguaro Glass Tint</title>
<link rel="stylesheet" href="https://fonts.googleapis.com/css2?family=Montserrat:wght@400;600;700&family=Open+Sans:wght@400;600&display=swap">
<style>
:root{
  --green:#6ed30d;
  --green-dark:#58b005;
  --dark:#222;
  --text:#444;
  --panel:#2f2f2f;
  --light:#f3f4f6;
  --white:#fff;
}
*{box-sizing:border-box;margin:0;padding:0}
html,body{width:1200px;height:3125px;overflow:hidden}
body{position:relative;background:var(--white);font-family:"Open Sans",Arial,sans-serif;color:var(--text)}
.abs{position:absolute}
h2.section-title{position:absolute;left:0;width:1200px;text-align:center;font-family:"Montserrat",Arial,sans-serif;font-weight:700;font-size:27px;color:var(--dark);letter-spacing:.5px}
.rule{position:absolute;left:550px;width:100px;height:4px;background:var(--green)}
.lead{position:absolute;left:0;width:1200px;text-align:center;font-size:12px;line-height:22px}
.btn{position:absolute;display:flex;align-items:center;justify-content:center;background:var(--green);color:var(--white);font-family:"Montserrat",Arial,sans-serif;font-weight:700;font-size:14px;text-transform:uppercase}

/* hero */
.hero-photo{position:absolute;left:0;top:0}
.brand{position:absolute;left:86px;top:46px;display:flex;align-items:center;gap:12px;font-family:"Montserrat",Arial,sans-serif;font-weight:700;font-size:26px;color:var(--white)}
.brand i{display:block;width:22px;height:22px;border-radius:50%;background:var(--green)}
.callout{position:absolute;right:86px;top:22px;font-family:"Montserrat",Arial,sans-serif;font-size:12px;font-weight:600;color:var(--white);display:flex;align-items:center;gap:8px}
.main-nav{position:absolute;left:462px;top:78px;display:flex;gap:0;font-family:"Montserrat",Arial,sans-serif;font-size:12px;font-weight:700;color:var(--white)}
.main-nav a{color:inherit;text-decoration:none;padding:0 22px;position:relative}
.main-nav a.active::before{content:"";position:absolute;left:0;right:0;top:-22px;height:4px;background:var(--green)}
.hero-copy{position:absolute;left:700px;top:296px;color:var(--white)}
.hero-copy .t1{font-family:"Montserrat",Arial,sans-serif;font-weight:700;font-size:54px;color:var(--green);line-height:64px}
.hero-copy .t2{font-family:"Montserrat",Arial,sans-serif;font-weight:400;font-size:54px;line-height:64px}
.hero-copy p{margin-top:18px;width:440px;font-size:19px;line-height:32px;font-weight:600}
.dots{position:absolute;left:570px;top:648px;display:flex;gap:8px}
.dots span{width:13px;height:13px;border-radius:50%;background:var(--white)}
.dots span.on{background:var(--green)}

/* services */
.service{position:absolute;width:340px;text-align:center;color:var(--white)}
.service .icon{width:100px;height:100px;margin:0 auto;transform:rotate(45deg);background:var(--green);border-radius:10px}
.service h3{margin-top:48px;font-family:"Montserrat",Arial,sans-serif;font-size:15px;font-weight:600;letter-spacing:.5px}
.service p{margin-top:14px;font-size:12px;line-height:26px}

/* gallery */
.tile{position:absolute}
.tile-label{position:absolute;left:87px;top:2090px;width:344px;height:48px;background:var(--green);color:var(--white);font-family:"Montserrat",Arial,sans-serif;font-weight:700;font-size:13px;display:flex;align-items:center;justify-content:center;text-transform:uppercase}

/* about */
.about-title{position:absolute;left:85px;top:2242px;font-family:"Montserrat",Arial,sans-serif;font-weight:700;font-size:26px;color:var(--dark)}
.about-copy{position:absolute;left:85px;width:520px;font-size:12px;line-height:24px}

/* contact */
.contact-title{position:absolute;left:0;width:1200px;top:2626px;text-align:center;font-family:"Montserrat",Arial,sans-serif;font-weight:700;font-size:26px;color:var(--white)}
.contact-sub{position:absolute;left:0;width:1200px;top:2672px;text-align:center;font-size:12px;color:var(--white)}
.field{position:absolute;background:var(--white);border-radius:3px;font-size:11px;color:#888;padding:12px 16px}
.send{position:absolute;left:529px;top:2958px;width:142px;height:50px;background:var(--panel);color:var(--white);font-family:"Montserrat",Arial,sans-serif;font-weight:700;font-size:14px;display:flex;align-items:center;justify-content:center}

/* footer */
.site-footer{position:absolute;left:0;top:3052px;width:1200px;height:73px;background:var(--panel);color:var(--white)}
.site-footer .copy{position:absolute;left:85px;top:28px;font-size:11px}
.social{position:absolute;left:906px;top:16px;display:flex;gap:8px}
.social span{width:40px;height:40px;border-radius:50%;border:2px solid var(--white)}
</style>
</head>
<body>

<!-- hero -->
<svg class="hero-photo" width="1200" height="700" viewBox="0 0 1200 700" role="img" aria-label="Silver sports car driving on an open road at sunset">
  <defs>
    <linearGradient id="sky" x1="0" y1="0" x2="0" y2="1">
      <stop offset="0" stop-color="#2a2624"/>
      <stop offset=".35" stop-color="#6b4a3a"/>
      <stop offset=".55" stop-color="#b9714a"/>
      <stop offset=".75" stop-color="#3b3532"/>
      <stop offset="1" stop-color="#1d1c1c"/>
    </linearGradient>
    <radialGradient id="car" cx=".28" cy=".42" r=".25">
      <stop offset="0" stop-color="#8a8d90" stop-opacity=".7"/>
      <stop offset="1" stop-color="#8a8d90" stop-opacity="0"/>
    </radialGradient>
  </defs>
  <polygon points="0,0 1200,0 1200,625 600,690 0,625" fill="url(#sky)"/>
  <polygon points="0,0 1200,0 1200,625 600,690 0,625" fill="url(#car)"/>
</svg>

<div class="brand"><i></i>Saguaro Glass Tint</div>
<div class="callout">
  <svg width="12" height="12" viewBox="0 0 24 24"><path fill="#fff" d="M6.6 10.8a15 15 0 0 0 6.6 6.6l2.2-2.2c.3-.3.7-.4 1-.2 1.1.4 2.3.6 3.6.6.6 0 1 .4 1 1V20c0 .6-.4 1-1 1A17 17 0 0 1 3 4c0-.6.4-1 1-1h3.5c.6 0 1 .4 1 1 0 1.3.2 2.5.6 3.6.1.3 0 .7-.2 1z"/></svg>
  GIVE US A CALL 480.555.0142
</div>
<nav class="main-nav">
  <a class="active">HOME</a><a>WINDOW FILM SERVICES</a><a>FILM</a><a>ABOUT</a><a>GALLERY</a><a>CONTACT</a>
</nav>
<div class="hero-copy">
  <div class="t1">SAGUARO</div>
  <div class="t2">WINDOW TINT</div>
  <p>Saguaro Tint owner Dale Morrow and his staff of professional Installers work</p>
</div>
<div class="btn" style="left:700px;top:517px;width:133px;height:45px">Read More</div>
<div class="dots"><span></span><span class="on"></span><span></span></div>

<!-- welcome -->
<svg class="abs" style="left:140px;top:850px" width="900" height="240" role="img" aria-label="Faded silver car in the background">
  <defs><radialGradient id="fade" cx=".5" cy=".55" r=".5"><stop offset="0" stop-color="#c9cbcd" stop-opacity=".45"/><stop offset="1" stop-color="#fff" stop-opacity="0"/></radialGradient></defs>
  <rect width="900" height="240" fill="url(#fade)"/>
</svg>
<h2 class="section-title" style="top:740px">WELCOME TO OUR COMPANY</h2>
<div class="rule" style="top:792px"></div>
<p class="lead" style="top:820px;left:250px;width:700px;line-height:27px">Saguaro Tint owner Dale Morrow and his staff of professional installers work with two of the world's finest window film manufacturers, Veralux and Clearon, whose superior products significantly reduce heat and UV rays while retaining color stability over long periods of solar exposure. The Veralux Prismline Automotive Window Film is a multilayer film combining heat entering through. While allowing 90% of light into your to 97% of heat-producing infrared light and block as much as 60% of the heat entering through</p>
<div class="btn" style="left:504px;top:952px;width:192px;height:48px;border-radius:24px">Read More Info</div>

<!-- services -->
<svg class="abs" style="left:0;top:1083px" width="1200" height="538">
  <polygon points="0,20 90,20 1090,20 1200,20 1200,538 0,538" fill="var(--panel)"/>
  <polygon points="0,0 90,20 0,62" fill="var(--green)"/>
  <polygon points="1090,20 1200,0 1200,62" fill="var(--green)"/>
</svg>
<h2 class="section-title" style="top:1161px;color:var(--white)">OUR SERVICES</h2>
<div class="rule" style="top:1213px"></div>
<p class="lead" style="top:1241px;color:var(--white)">Saguaro Tint owner Dale Morrow and his staff of professional installers work with two of the world's finest window film manufacturers</p>
<div class="service" style="left:80px;top:1310px"><div class="icon"></div><h3>AUTOMOTIVE FILM</h3><p>Saguaro Tint owner Dale Morrow and his staff of professional installers work with two of the world's finest window film manufacturers</p></div>
<div class="service" style="left:430px;top:1310px"><div class="icon"></div><h3>COMMERCIAL &amp; RESIDENTIAL</h3><p>Saguaro Tint owner Dale Morrow and his staff of professional installers work with two of the world's finest window film manufacturers</p></div>
<div class="service" style="left:780px;top:1310px"><div class="icon"></div><h3>CLEAR BRA</h3><p>Saguaro Tint owner Dale Morrow and his staff of professional installers work with two of the world's finest window film manufacturers</p></div>

<!-- gallery -->
<h2 class="section-title" style="top:1663px">PHOTO GALLERY</h2>
<div class="rule" style="top:1713px"></div>
<p class="lead" style="top:1735px">Saguaro Tint owner Dale Morrow and his staff of professional installers work with two of the world's finest window film manufacturers</p>
<div class="tile" style="left:87px;top:1790px;width:532px;height:348px;background:linear-gradient(135deg,#1f1f22,#55585c 55%,#2a2b2e)" role="img" aria-label="Red sedan speeding on a highway"></div>
<div class="tile-label">Prismline Automotive Window Film</div>
<div class="tile" style="left:635px;top:1790px;width:234px;height:165px;background:linear-gradient(180deg,#d7b98a,#8a7a5a 60%,#4a4036)" role="img" aria-label="Black SUV on a desert hillside"></div>
<div class="tile" style="left:879px;top:1790px;width:236px;height:165px;background:linear-gradient(180deg,#e6e1d8,#a8a29a 60%,#b4423e)" role="img" aria-label="Red convertible on a sunny road"></div>
<div class="tile" style="left:635px;top:1971px;width:234px;height:167px;background:linear-gradient(180deg,#2d4f78,#4f6f91 50%,#c03a4e)" role="img" aria-label="Pink sports car under blue sky"></div>
<div class="tile" style="left:879px;top:1971px;width:236px;height:167px;background:linear-gradient(180deg,#456c8e,#6d8aa2 50%,#cfd3d6)" role="img" aria-label="White concept sports car"></div>

<!-- about -->
<div class="abs" style="left:0;top:2198px;width:1200px;height:396px;background:var(--light)"></div>
<svg class="abs" style="left:0;top:2198px" width="1200" height="396" role="img" aria-label="White sports car parked in a sunny park">
  <defs><linearGradient id="park" x1="0" y1="0" x2="1" y2="1"><stop offset="0" stop-color="#f3e7b8"/><stop offset=".4" stop-color="#8ea45a"/><stop offset="1" stop-color="#3d4a2c"/></linearGradient></defs>
  <polygon points="688,0 1200,0 1200,396 562,396" fill="url(#park)"/>
</svg>
<h2 class="about-title">ABOUT US</h2>
<p class="about-copy" style="top:2318px">Window film is a sheet of coating that, with proper installation by Saguaro Tint, can deliver energy savings similar to that offered by premium replacement windows — but without the expense of replacement. On existing home windows, including dual pane and low e, the process is usually immediate improvements in comfort, efficiency and glare reduction.</p>
<p class="about-copy" style="top:2453px">A wide range of protective film is available. These include anti-graffiti, nonreflective, decorative, dual-reflective and ceramic. Choose, too, from many shades, almost clear to dark. And, because window film is considered carbon negative, some products qualify for sustainable home credits and energy rebates.</p>

<!-- contact -->
<div class="abs" style="left:0;top:2594px;width:1200px;height:458px;background:linear-gradient(180deg,var(--green),var(--green-dark))"></div>
<h2 class="contact-title">CONTACT US</h2>
<p class="contact-sub">Sed ut perspiciatis unde omnis iste natus error sit voluptatem accusantium doloremque laudantium</p>
<div class="field" style="left:298px;top:2727px;width:292px;height:44px">Name :</div>
<div class="field" style="left:602px;top:2727px;width:290px;height:44px">Phone :</div>
<div class="field" style="left:298px;top:2779px;width:292px;height:44px">Email :</div>
<div class="field" style="left:602px;top:2779px;width:290px;height:44px">Website :</div>
<div class="field" style="left:298px;top:2831px;width:594px;height:104px">Comments :</div>
<div class="send">SEND</div>

<!-- footer -->
<footer class="site-footer">
  <div class="copy">© Copy Rights 2017 Saguaro Glass Tint All rights reserved.</div>
  <div class="social" aria-label="Social links"><span></span><span></span><span></span><span></span><span></span></div>
</footer>

</body>
</html>
```